175th Anniversary of Family Owned Funeral Home Pole Banners

We are family owned and operated funeral home in the Greater Cincinnati area and operate 3 funeral homes and a cremation center and we will be celebrating our 175th anniversary in 2015. The communities we serve look to us as leaders in the community and we are very well recognized. In preparation for next year, part of our planning includes placing pole banners in our local communities and our funeral home parking areas. The banner dimensions will be 30 x 60. We need for the banners to display a great message of tradition and excellence. Our website is www.brannockwelde.com I have uploaded an example of a pole banner as well as our logo(s).
Updates
Original artwork has been uploaded if needed.
Industry/Entity Type
Funeral Home

```html
<!DOCTYPE html>
<html lang="en">
<head>
<meta charset="utf-8">
<title>Brannock Welde 175th Anniversary Pole Banner</title>
<link href="https://fonts.googleapis.com/css2?family=Open+Sans:wght@400;600;800&display=swap" rel="stylesheet">
<style>
  :root {
    --page-bg: #dcdcdc;
    --banner-white: #ffffff;
    --headline-yellow: #ffe100;
    --accent-blue: #2f6487;
    --accent-cyan: #3fb6d6;
    --brand-navy: #2c4a6e;
    --photo-warm-a: #8a6a4e;
    --photo-warm-b: #c9a57c;
    --photo-dark-a: #1d2b45;
    --photo-dark-b: #3a2430;
  }
  html, body {
    margin: 0;
    padding: 0;
    width: 1200px;
    height: 1051px;
    overflow: hidden;
    background: var(--page-bg);
    font-family: "Open Sans", Arial, sans-serif;
  }
  .banner {
    position: absolute;
    left: 420px;
    top: 30px;
    width: 360px;
    height: 990px;
    background: var(--banner-white);
    box-shadow: 0 4px 18px rgba(0,0,0,0.15);
  }
  .banner svg { display: block; }
  .url { font-size: 10px; font-weight: 800; letter-spacing: 2.6px; fill: var(--headline-yellow); }
  .celebrating { font-size: 38px; font-weight: 800; fill: var(--headline-yellow); }
  .years { font-size: 146px; font-weight: 800; fill: var(--headline-yellow); letter-spacing: -4px; }
  .ordinal { font-size: 22px; font-weight: 800; fill: var(--headline-yellow); }
  .anniversary { font-size: 22px; font-weight: 800; fill: var(--headline-yellow); }
  .anniversary .year-note { font-weight: 400; }
  .brand-name { font-size: 22px; font-weight: 600; fill: var(--brand-navy); }
  .brand-tagline { font-size: 11.5px; font-weight: 400; fill: var(--brand-navy); }
</style>
</head>
<body>
  <div class="banner">
    <svg width="360" height="990" viewBox="0 0 360 990" xmlns="http://www.w3.org/2000/svg">
      <defs>
        <linearGradient id="warmPhoto" x1="0" y1="0" x2="1" y2="1">
          <stop offset="0" stop-color="#6d4f5a"/>
          <stop offset="0.5" stop-color="var(--photo-warm-b)"/>
          <stop offset="1" stop-color="var(--photo-warm-a)"/>
        </linearGradient>
        <linearGradient id="darkPhoto" x1="0" y1="0" x2="1" y2="1">
          <stop offset="0" stop-color="#2b3d57"/>
          <stop offset="0.55" stop-color="var(--photo-dark-b)"/>
          <stop offset="1" stop-color="var(--photo-dark-a)"/>
        </linearGradient>
      </defs>

      <polygon class="photo-casket" role="img" aria-label="Photo of a wooden casket topped with a floral arrangement"
               points="16,12 342,12 342,235 16,420" fill="url(#warmPhoto)"/>

      <polygon class="photo-roses" role="img" aria-label="Photo of dark red roses in a funeral bouquet"
               points="16,420 342,235 342,718 183,857 16,735" fill="url(#darkPhoto)"/>

      <line class="divider-line" x1="16" y1="440" x2="342" y2="255" stroke="var(--accent-cyan)" stroke-width="2"/>

      <polygon class="chevron-band" points="183,857 342,718 342,690 200,815" fill="var(--accent-blue)"/>

      <text class="url" x="60" y="505">WWW.BRANNOCKWELDE.COM</text>
      <text class="celebrating" x="56" y="546">CELEBRATING</text>
      <text class="years" x="48" y="662">175</text>
      <text class="ordinal" x="292" y="590">TH</text>
      <text class="anniversary" x="58" y="698">ANNIVERSARY<tspan class="year-note" dx="4">IN 2015</tspan></text>

      <circle class="brand-mark" cx="72" cy="925" r="12" fill="var(--brand-navy)"/>
      <text class="brand-name" x="94" y="932">Brannock Welde</text>
      <text class="brand-tagline" x="62" y="956">Family Funeral Homes &amp; Cremation Center</text>
    </svg>
  </div>
</body>
</html>
```